Coastline Premier Retreats Business Card Design

Design a business card for Coastline Premier Retreats. Look at the website for colors and reference. Card should have logo, name, title, office number, mobile number, email, URL and a tagline like, "Luxury Hotel & Resort Email Marketing" (This might change).

https://www.coastlinepremierretreats.example

The rest I will leave up to your imagination.

Contact Information for Business Card

Logo, name, title, office number, mobile number, email, URL and a tagline like, "Luxury Hotel & Resort Email Marketing" (This might change).

```html
<!DOCTYPE html>
<html lang="en">
<head>
<meta charset="utf-8">
<title>Coastline Premier Retreats – Business Card</title>
<link rel="stylesheet" href="https://fonts.googleapis.com/css2?family=Montserrat:wght@700;800&family=Mulish:wght@400;500&display=swap">
<style>
  :root {
    --backdrop: #d0d3d4;
    --ink: #050608;
    --orange: #f37521;
    --white: #ffffff;
    --edge: #1a8fb3;
  }
  * { box-sizing: border-box; margin: 0; padding: 0; }
  html, body { width: 1200px; height: 1200px; overflow: hidden; }
  body {
    background: var(--backdrop);
    font-family: "Mulish", sans-serif;
    color: var(--white);
    position: relative;
  }
  .card {
    position: absolute;
    left: 150px;
    width: 900px;
    height: 514px;
    overflow: hidden;
    border-bottom: 4px solid var(--edge);
  }
  .card--back { top: 70px; background: var(--ink); }
  .card--front { top: 616px; background: var(--orange); }

  .wordmark {
    position: absolute;
    left: 0; right: 0;
    text-align: center;
    font-family: "Montserrat", sans-serif;
    font-weight: 800;
    text-transform: uppercase;
    color: var(--white);
    letter-spacing: 1px;
    line-height: 1.05;
  }
  .card--back .wordmark { top: 120px; font-size: 56px; }
  .card--front .wordmark { top: 46px; font-size: 46px; }

  .rule {
    position: absolute;
    height: 2px;
    background: var(--white);
  }
  .card--back .rule { top: 318px; left: 0; right: 0; }
  .card--front .rule { top: 236px; left: 60px; right: 60px; }

  .tagline {
    position: absolute;
    top: 294px;
    left: 50%;
    transform: translateX(-50%);
    background: var(--orange);
    color: var(--white);
    border-radius: 26px;
    padding: 12px 36px;
    font-size: 24px;
    white-space: nowrap;
  }

  .person {
    position: absolute;
    top: 150px;
    right: 200px;
    text-align: left;
  }
  .person__name {
    font-family: "Montserrat", sans-serif;
    font-weight: 700;
    font-size: 34px;
  }
  .person__title { font-size: 22px; margin-top: 2px; }

  .contacts {
    position: absolute;
    top: 266px;
    left: 60px;
    list-style: none;
    font-size: 22px;
    line-height: 1.55;
  }
  .contacts li { display: flex; align-items: center; gap: 10px; }
  .contacts svg { width: 18px; height: 18px; flex: none; }

  .address {
    position: absolute;
    right: 60px;
    bottom: 44px;
    text-align: right;
    font-style: normal;
    font-size: 24px;
    line-height: 1.35;
  }
</style>
</head>
<body>

<section class="card card--back" aria-label="Card back">
  <p class="wordmark">Coastline<br>Premier Retreats</p>
  <div class="rule"></div>
  <p class="tagline">Luxury Hotel &amp; Resort Email Marketing</p>
</section>

<section class="card card--front" aria-label="Card front">
  <p class="wordmark">Coastline Premier Retreats</p>

  <div class="person">
    <p class="person__name">Daniel Marsh</p>
    <p class="person__title">Founder &amp; Director</p>
  </div>

  <div class="rule"></div>

  <ul class="contacts">
    <li>
      <svg viewBox="0 0 24 24" fill="currentColor" aria-hidden="true"><path d="M6.6 10.8a15 15 0 0 0 6.6 6.6l2.2-2.2a1 1 0 0 1 1-.25 11.4 11.4 0 0 0 3.6.57 1 1 0 0 1 1 1V20a1 1 0 0 1-1 1A17 17 0 0 1 3 4a1 1 0 0 1 1-1h3.5a1 1 0 0 1 1 1c0 1.25.2 2.45.57 3.57a1 1 0 0 1-.25 1z"/></svg>
      555.014.2200
    </li>
    <li>
      <svg viewBox="0 0 24 24" fill="none" stroke="currentColor" stroke-width="2" aria-hidden="true"><rect x="6" y="2" width="12" height="20" rx="2"/><line x1="11" y1="18" x2="13" y2="18"/></svg>
      555-019-3471
    </li>
    <li>
      <svg viewBox="0 0 24 24" fill="currentColor" aria-hidden="true"><path d="M2 5h20v14H2z M2 5l10 8 10-8" stroke="var(--orange)" stroke-width="1.5"/></svg>
      info@coastlinepremierretreats.example
    </li>
    <li>
      <svg viewBox="0 0 24 24" fill="none" stroke="currentColor" stroke-width="2" aria-hidden="true"><circle cx="12" cy="12" r="10"/><path d="M2 12h20M12 2a15 15 0 0 1 0 20M12 2a15 15 0 0 0 0 20"/></svg>
      www.coastlinepremierretreats.example
    </li>
  </ul>

  <address class="address">
    North America,<br>
    4178 Harbor View Lane<br>
    Port Ellis Maine 04999
  </address>
</section>

</body>
</html>
```